Clean Modern Skin Product branding/ label.

I need a label for a skincare line. The company is Dermaloft but product names will vary. A couple products to list are:
Sensitive Cleanser, Lumeno, Repair, Halo up, Mendora, Mendora Plus, Mendora Intense, Tavelo, Balance and Vivanto.

I would like the color scheme to be muted greens, grays, tourquise. The bottles are white, boston shaped with pumps, and ounces are 2, 4, 8, 16 ounces. When I choose the design, I can give you exact label sizes. Along with the ingredience already on the product label.

The look I desire is clean, minimal. A modern, organic look. Ideas that come to mind are a Veloraine,https://www.veloraine-example.com/product/2846/37204/3-step/step-2-exfoliate/clarifying-lotion-1 and the simplicity of Bo Tarn.

Both styles high light the name, in this case Dermaloft, and then the specific product.

My product is clean utilizing pure ingredients rather that a bunch fillers and binders. When I work with my clients I normally will say we need to "restore the balance" from over use of harsh products. That is why this lines works. It restores the skin to it's natural state. The process is simple, so I would like the label to reflect that simplicity.

Target Market(s)

Anyone with sensitive skin. So gender neutral

Industry/Entity Type

Skin Care Product

Font styles to use
Serif
Sans Serif
Decorative

Colors
acd037
33b8a4
fcfefd
85cae6
d3d3d3

Requirements
Must have
• Logo, name of product and color identity for cleanser, Active products, moisturizers
• I am thinking we could have one color for a cleanser and a space where I can put a sticker on which cleanser it is. Acne Cleasner, Sensitive Cleanser, and Cleanser.
Nice to have
• Not sure....suprise me. I would like the font to stay the same on the DERMALOFT, but you can change color, or color of leaf.
Should not have
• Too busy, too crowded or look like every other skincare line

```html
<!DOCTYPE html>
<html lang="en">
<head>
<meta charset="utf-8">
<title>Dermaloft Label Series</title>
<link rel="stylesheet" href="https://fonts.googleapis.com/css2?family=League+Spartan:wght@300;400;700&family=Tinos&display=swap">
<style>
  :root {
    --page: #ffffff;
    --ink-light: #ffffff;
    --plus-a: #d4cdee;
    --plus-b: #b6c6f0;
    --plus-c: #c9bde6;
    --cleanser-a: #e2c7ea;
    --cleanser-b: #c6a3d8;
    --cleanser-c: #d8b7e0;
    --intense-a: #c9cde2;
    --intense-b: #a6dccf;
    --intense-c: #bcd3dc;
  }
  * { margin: 0; padding: 0; box-sizing: border-box; }
  html, body {
    width: 1200px;
    height: 748px;
    overflow: hidden;
    background: var(--page);
  }
  .series {
    position: relative;
    width: 1200px;
    height: 748px;
  }
  .label {
    position: absolute;
    top: 327px;
    width: 229px;
    height: 322px;
    color: var(--ink-light);
    font-family: "League Spartan", sans-serif;
  }
  .label--plus { left: 208px; }
  .label--cleanser { left: 498px; }
  .label--intense { left: 782px; }
  .label__surface {
    position: absolute;
    inset: 0;
  }
  .label--plus .label__surface {
    background:
      radial-gradient(ellipse at 20% 85%, var(--plus-b), transparent 60%),
      linear-gradient(160deg, var(--plus-a) 0%, var(--plus-c) 55%, var(--plus-b) 100%);
  }
  .label--cleanser .label__surface {
    background:
      radial-gradient(ellipse at 70% 70%, var(--cleanser-b), transparent 60%),
      linear-gradient(160deg, var(--cleanser-a) 0%, var(--cleanser-c) 50%, var(--cleanser-b) 100%);
  }
  .label--intense .label__surface {
    background:
      radial-gradient(ellipse at 80% 75%, var(--intense-b), transparent 60%),
      linear-gradient(160deg, var(--intense-a) 0%, var(--intense-c) 55%, var(--intense-b) 100%);
  }
  .label__content {
    position: absolute;
    left: 53px;
    top: 40px;
    right: 16px;
  }
  .brand {
    font-family: "League Spartan", sans-serif;
    font-weight: 400;
    font-size: 21px;
    letter-spacing: -0.3px;
    line-height: 1;
  }
  .product-name {
    margin-top: 26px;
    font-weight: 700;
    font-size: 25px;
    line-height: 28px;
    letter-spacing: 0.2px;
  }
  .tagline {
    margin-top: 14px;
    font-weight: 300;
    font-size: 8px;
    letter-spacing: 0.3px;
    text-transform: uppercase;
  }
  .description {
    margin-top: 4px;
    font-family: "Tinos", serif;
    font-size: 9px;
    line-height: 11.2px;
    width: 160px;
  }
  .volume {
    margin-top: 13px;
    font-weight: 700;
    font-size: 9px;
    letter-spacing: 0.3px;
  }
</style>
</head>
<body>
<main class="series">

  <section class="label label--plus">
    <div class="label__surface" role="img" aria-label="Soft lavender and blue marbled liquid pattern"></div>
    <div class="label__content">
      <div class="brand">Dermaloft</div>
      <h2 class="product-name">Mendora<br>Plus.</h2>
      <p class="tagline">Restore the balance</p>
      <p class="description">Lilutpat ut wisi eniml orem ipsum dolor sit amet, consectetuer adipiscing elit, sed diam nonummy nibh euismod tincidunt ut laoreet dolore magna aliquam erat volutpat. Ut wisi enim ad minim veniam, quis nostrud exerci tation ullamcorper suscipit lobortis nisl ut aliquip ex ea commodo consequat.</p>
      <p class="volume">16FL.OZ — 500ML</p>
    </div>
  </section>

  <section class="label label--cleanser">
    <div class="label__surface" role="img" aria-label="Soft pink and lilac marbled liquid pattern"></div>
    <div class="label__content">
      <div class="brand">Dermaloft</div>
      <h2 class="product-name">Sensitive<br>Cleanser.</h2>
      <p class="tagline">Restore the balance</p>
      <p class="description">Lilutpat ut wisi eniml orem ipsum dolor sit amet, consectetuer adipiscing elit, sed diam nonummy nibh euismod tincidunt ut laoreet dolore magna aliquam erat volutpat. Ut wisi enim ad minim veniam, quis nostrud exerci tation ullamcorper suscipit lobortis nisl ut aliquip ex ea commodo consequat.</p>
      <p class="volume">16FL.OZ — 500ML</p>
    </div>
  </section>

  <section class="label label--intense">
    <div class="label__surface" role="img" aria-label="Soft mint and grey-blue marbled liquid pattern"></div>
    <div class="label__content">
      <div class="brand">Dermaloft</div>
      <h2 class="product-name">Mendora<br>Intense.</h2>
      <p class="tagline">Restore the balance</p>
      <p class="description">Lilutpat ut wisi eniml orem ipsum dolor sit amet, consectetuer adipiscing elit, sed diam nonummy nibh euismod tincidunt ut laoreet dolore magna aliquam erat volutpat. Ut wisi enim ad minim veniam, quis nostrud exerci tation ullamcorper suscipit lobortis nisl ut aliquip ex ea commodo consequat.</p>
      <p class="volume">16FL.OZ — 500ML</p>
    </div>
  </section>

</main>
</body>
</html>
```